Business Card: RW Office Partners - Your organised problem solver

Business Name: RW Office Partners
Website: www.rwofficepartners.com.au
Email: marisol@rwofficepartners.com.au
Mobile: 61 482 907 236
Facebook: @rwofficepartners
Instrgram: @rwofficepartners

Brading Colours:
HEX
#986474
#ddccd3
#7a8498
#c9d8e4
#000000
#ffffff

Tag Line: Your dependable task handler

Link to DRAFT website:
https://deskhelpcollective.wixsite.com/rw-office-partners

About Page from the website:
My name is Marisol Wrenfield, and I would love to assist you to become more productive in your day to day and achieve your business and personal goals.
My mission is to give you time, time to work on the important tasks of your business or to be able to spend more time with your family. I will take on the tasks you don’t have time for, don’t know well or simply don’t like to do.
I have an extensive background in Administration, Tender Coordination, Document Control, WHS and Quality Management working primarily in the Construction, Mining and Corporate World.
I am passionate about being organised, having order and making things in your life (and mine) easier! I love to watch something unfold and grow into something amazing! I am known for being the go-to problem solver, the organiser of all things, producing high standards of work even under pressure. I’m also a confident communicator, and I understand that you’re busy running your business.

Target Market(s)

Small to Medium Business who require assistance in their business by a virtual assistant.

Industry/Entity Type

Virtual Assistant

Contact Information for Business Card

Mobile: 61 482 907 236

Font styles to use
Sans Serif

Colors
ffffff

Requirements
Must have
• Branding Colours as outlined.
Contact Details as outlined.
Logo as provided.
Proper contact details - mobile, facebook, instragm, website.
Simple, Elegant, very clean looking.
Should not have
• Note cute with pictures.
Not too girly as still want to market to construction companies.

```html
<!DOCTYPE html>
<html lang="en">
<head>
<meta charset="utf-8">
<title>RW Office Partners – Business Card</title>
<link rel="stylesheet" href="https://fonts.googleapis.com/css2?family=Roboto:wght@300;400;500&display=swap">
<style>
  :root {
    --page-bg: #e9e8ea;
    --card-bg: #1d1d1f;
    --card-bg-deep: #171718;
    --pattern-tone: #242426;
    --brand-rose: #986474;
    --brand-rose-light: #ddccd3;
    --brand-slate: #7a8498;
    --brand-mist: #c9d8e4;
    --text-contact: #9ea6b8;
    --wordmark: #8e96ad;
  }
  * { margin: 0; padding: 0; box-sizing: border-box; }
  html, body {
    width: 1200px;
    height: 900px;
    overflow: hidden;
    background: var(--page-bg);
    font-family: "Roboto", sans-serif;
  }
  .canvas {
    width: 1200px;
    height: 900px;
    display: flex;
    flex-direction: column;
    align-items: center;
    justify-content: center;
    gap: 44px;
  }
  .card {
    position: relative;
    width: 672px;
    height: 384px;
    background: var(--card-bg);
    box-shadow: 0 10px 30px rgba(0, 0, 0, 0.25);
    overflow: hidden;
  }

  /* Front */
  .contact-list {
    position: absolute;
    left: 44px;
    top: 118px;
    list-style: none;
  }
  .contact-item {
    display: flex;
    align-items: center;
    gap: 8px;
    font-size: 17px;
    font-weight: 300;
    color: var(--text-contact);
    line-height: 25px;
    letter-spacing: 0.2px;
  }
  .contact-icon {
    width: 13px;
    height: 13px;
    flex: none;
  }
  .social-mark {
    width: 11px;
    height: 11px;
    background: var(--brand-rose);
    border-radius: 2px;
    flex: none;
  }
  .social-marks {
    display: flex;
    gap: 4px;
  }
  .tagline {
    position: absolute;
    left: 44px;
    top: 240px;
    font-size: 17px;
    font-weight: 300;
    color: var(--brand-rose);
    letter-spacing: 0.2px;
  }
  .brand-name {
    position: absolute;
    right: 44px;
    top: 150px;
    width: 230px;
    font-size: 32px;
    font-weight: 500;
    line-height: 34px;
    text-transform: uppercase;
    letter-spacing: 1px;
    color: var(--wordmark);
    text-align: left;
  }

  /* Back */
  .card-back {
    background: var(--card-bg-deep);
  }
  .back-pattern {
    position: absolute;
    inset: 0;
    background: linear-gradient(135deg, var(--card-bg-deep), var(--pattern-tone) 50%, var(--card-bg-deep));
  }
  .back-brand {
    position: absolute;
    right: 40px;
    bottom: 34px;
    font-size: 24px;
    font-weight: 500;
    text-transform: uppercase;
    letter-spacing: 1px;
    color: var(--brand-rose);
  }
</style>
</head>
<body>
<main class="canvas">
  <section class="card card-front" aria-label="Card front">
    <ul class="contact-list">
      <li class="contact-item">
        <svg class="contact-icon" viewBox="0 0 16 16" aria-hidden="true">
          <path d="M4 1.5 L6.5 4.5 L5 6.2 C5.8 8 7.8 10 9.8 11 L11.5 9.5 L14.5 12 L12.8 14.3 C7.5 14 2 8.5 1.7 3.2 Z" fill="var(--brand-rose-light)"/>
        </svg>
        61 482 907 236
      </li>
      <li class="contact-item">
        <svg class="contact-icon" viewBox="0 0 16 16" aria-hidden="true">
          <rect x="1" y="3.5" width="14" height="9" rx="1" fill="var(--brand-rose-light)"/>
          <path d="M1.5 4 L8 9 L14.5 4" fill="none" stroke="var(--card-bg)" stroke-width="1.2"/>
        </svg>
        marisol@rwofficepartners.com.au
      </li>
      <li class="contact-item">
        <svg class="contact-icon" viewBox="0 0 16 16" aria-hidden="true">
          <circle cx="8" cy="8" r="6.5" fill="none" stroke="var(--brand-rose-light)" stroke-width="1.4"/>
          <ellipse cx="8" cy="8" rx="2.8" ry="6.5" fill="none" stroke="var(--brand-rose-light)" stroke-width="1.1"/>
          <line x1="1.5" y1="8" x2="14.5" y2="8" stroke="var(--brand-rose-light)" stroke-width="1.1"/>
        </svg>
        www.rwofficepartners.com.au
      </li>
      <li class="contact-item">
        <span class="social-marks" aria-hidden="true">
          <span class="social-mark"></span>
          <span class="social-mark"></span>
        </span>
        @rwofficepartners
      </li>
    </ul>
    <p class="tagline">Your dependable task handler</p>
    <h1 class="brand-name">RW Office Partners</h1>
  </section>

  <section class="card card-back" aria-label="Card back">
    <div class="back-pattern" role="img" aria-label="Faint tone-on-tone repeating brand monogram pattern"></div>
    <p class="back-brand">RW Office Partners</p>
  </section>
</main>
</body>
</html>
```